Fernwick Landscaping Folder Design

I need a graphic designer to design a folder so we can insert informational sheets inside it for customers. The folder must include the company logo, project images, on front and back of folder and slogan " The Experience You Want, The Service You Expect, And The Value You Deserve'

Folder to also include phone numbers : 416 555 0193 as well as the website: www.fernwicklandscaping.example as well as we gurantee a 24 month warranty.

I have attached sample of size we need.

Pixel Harbor has also done something similar for me for Tollbridge Landscapes

Target Market(s)

geared toward home owners & commercial/industrial

Industry/Entity Type

Landscaping

Font styles to use
Other font styles liked:
• open to new trendy font

Requirements
Must have
• Telephone Number, email address, slogan, images,
Nice to have
• images of completed projects incorporated into the front and back of folder as well as the logo
Should not have
• n/a

```html
<!DOCTYPE html>
<html lang="en">
<head>
<meta charset="utf-8">
<title>Fernwick Landscaping Folder</title>
<link rel="stylesheet" href="https://fonts.googleapis.com/css2?family=Oswald:wght@500;700&family=Roboto:wght@400;500&display=swap">
<style>
  :root {
    --stage: #e9e7e3;
    --paper: #ffffff;
    --slogan-light: #ededed;
    --slogan-strong: #dadada;
    --ink: #4a4a4a;
    --band: #6b6b6b;
    --band-text: #ffffff;
    --photo-walk: linear-gradient(135deg, #6f7d52 0%, #9a9890 55%, #c7c4bc 100%);
    --photo-pool: linear-gradient(160deg, #3b4a3a 0%, #2f6fb8 55%, #5fa6e8 100%);
    --photo-garage: linear-gradient(135deg, #d9d2c2 0%, #b8ab93 60%, #978a72 100%);
    --photo-drive: linear-gradient(170deg, #4f5a3c 0%, #7b7a63 40%, #d8d6d0 100%);
  }
  * { margin: 0; padding: 0; box-sizing: border-box; }
  html, body { width: 1200px; height: 848px; overflow: hidden; }
  body {
    background: var(--stage);
    font-family: "Roboto", Arial, sans-serif;
    position: relative;
  }
  .folder-panel {
    position: absolute;
    top: 127px;
    width: 420px;
    height: 594px;
    background: var(--paper);
    box-shadow: 0 6px 18px rgba(0,0,0,0.18);
  }
  .folder-front { left: 150px; }
  .folder-back { left: 630px; }

  /* Front cover */
  .slogan {
    position: absolute;
    left: 30px;
    top: 120px;
    font-family: "Oswald", "Arial Narrow", sans-serif;
    font-weight: 700;
    font-size: 54px;
    line-height: 0.98;
    text-transform: uppercase;
    letter-spacing: 0.5px;
  }
  .slogan .light { color: var(--slogan-light); display: block; }
  .slogan .strong { color: var(--slogan-strong); display: block; }
  .brand-name {
    position: absolute;
    right: 30px;
    bottom: 118px;
    display: flex;
    align-items: center;
    gap: 8px;
    font-family: "Oswald", "Arial Narrow", sans-serif;
    font-weight: 500;
    font-size: 17px;
    color: var(--ink);
    letter-spacing: 1px;
    text-transform: uppercase;
  }
  .brand-mark { width: 12px; height: 12px; background: var(--ink); }

  /* Back cover */
  .project-gallery {
    position: absolute;
    left: 22px;
    top: 24px;
    width: 376px;
    display: grid;
    grid-template-columns: 56% 1fr;
    grid-template-rows: 118px 82px 128px;
    gap: 4px;
  }
  .project-photo { width: 100%; height: 100%; }
  .photo-walkway { grid-column: 1 / 3; background: var(--photo-walk); }
  .photo-pool { background: var(--photo-pool); }
  .photo-garage { background: var(--photo-garage); }
  .photo-driveway { grid-column: 1 / 3; background: var(--photo-drive); }
  .warranty-band {
    position: absolute;
    left: 22px;
    top: 366px;
    width: 376px;
    height: 26px;
    background: var(--band);
    color: var(--band-text);
    font-size: 10px;
    font-weight: 500;
    letter-spacing: 0.8px;
    text-transform: uppercase;
    display: flex;
    align-items: center;
    justify-content: center;
  }
  .contact-list {
    position: absolute;
    top: 404px;
    left: 0;
    width: 100%;
    list-style: none;
    display: flex;
    flex-direction: column;
    align-items: center;
    gap: 5px;
    font-size: 11px;
    color: var(--ink);
  }
  .contact-item { display: flex; align-items: center; gap: 6px; width: 200px; }
  .contact-icon { width: 10px; height: 10px; flex: none; }
</style>
</head>
<body>
  <section class="folder-panel folder-front" aria-label="Folder front cover">
    <h1 class="slogan">
      <span class="light">The Experience</span>
      <span class="strong">You Want,</span>
      <span class="light">The Service</span>
      <span class="strong">You Expect,</span>
      <span class="light">And The Value</span>
      <span class="strong">You Deserve</span>
    </h1>
    <div class="brand-name"><span class="brand-mark"></span>Fernwick Landscaping Ltd.</div>
  </section>

  <section class="folder-panel folder-back" aria-label="Folder back cover">
    <div class="project-gallery">
      <div class="project-photo photo-walkway" role="img" aria-label="Stone walkway with garden beds and steps"></div>
      <div class="project-photo photo-pool" role="img" aria-label="Lit backyard pool with stone surround at dusk"></div>
      <div class="project-photo photo-garage" role="img" aria-label="Interlocking paver driveway in front of a garage"></div>
      <div class="project-photo photo-driveway" role="img" aria-label="Curved concrete driveway with lawn and trees"></div>
    </div>
    <div class="warranty-band">We gurantee a 24 month warranty</div>
    <ul class="contact-list">
      <li class="contact-item">
        <svg class="contact-icon" viewBox="0 0 10 10" aria-hidden="true"><circle cx="5" cy="5" r="5" fill="#4a4a4a"/><path d="M3.2 2.6l1 1-.5.6c.3.7.9 1.3 1.6 1.6l.6-.5 1 1-.6.8C4.7 7 3 5.3 2.5 3.2z" fill="#fff"/></svg>
        416 555 0193
      </li>
      <li class="contact-item">
        <svg class="contact-icon" viewBox="0 0 10 10" aria-hidden="true"><circle cx="5" cy="5" r="4.4" fill="none" stroke="#4a4a4a" stroke-width="1.1"/><ellipse cx="5" cy="5" rx="1.8" ry="4.4" fill="none" stroke="#4a4a4a" stroke-width="0.8"/><line x1="0.6" y1="5" x2="9.4" y2="5" stroke="#4a4a4a" stroke-width="0.8"/></svg>
        www.fernwicklandscaping.example
      </li>
    </ul>
  </section>
</body>
</html>
```